Promotional business a5 Notepad design

I am looking for a custom a5 notepad design as a promotional item to give away to customers etc.
Attached will be a desk planner we had designed feel free to use as a reference.
We want the notepad to have lines running horizontal not squares like the desk planner example.

Industry/Entity Type

Hydraulic / industrial

Colors

Designer to choose colors to be used in the design.

```html
<!DOCTYPE html>
<html lang="en">
<head>
<meta charset="utf-8">
<title>Meridian Hose &amp; Couplings – A5 Notepad</title>
<link href="https://fonts.googleapis.com/css2?family=Roboto:wght@400;700&display=swap" rel="stylesheet">
<style>
  :root {
    --backdrop: #dcdcdc;
    --paper: #f7f7f7;
    --rule: #c9cfe6;
    --brand-blue: #2f3e9e;
    --footer-black: #141414;
    --footer-text: #e6e6e6;
    --mark-dark: #141414;
  }
  * { margin: 0; padding: 0; box-sizing: border-box; }
  html, body {
    width: 1153px;
    height: 1200px;
    overflow: hidden;
    background: var(--backdrop);
    font-family: "Roboto", sans-serif;
  }
  .notepad {
    position: absolute;
    left: 170px;
    top: 25px;
    width: 812px;
    height: 1150px;
    background: var(--paper);
  }
  .brand {
    position: absolute;
    top: 74px;
    left: 0;
    width: 100%;
    display: flex;
    justify-content: center;
    align-items: center;
    gap: 14px;
  }
  .brand-dot {
    width: 46px;
    height: 46px;
    border-radius: 50%;
    background: var(--mark-dark);
  }
  .brand-name {
    font-weight: 700;
    font-size: 27px;
    letter-spacing: 1.5px;
    color: var(--brand-blue);
    text-transform: uppercase;
  }
  .ruled-area {
    position: absolute;
    left: 55px;
    top: 236px;
    width: 715px;
    height: 774px;
    background-image: repeating-linear-gradient(
      to bottom,
      var(--rule) 0,
      var(--rule) 1px,
      transparent 1px,
      transparent 33.6px
    );
  }
  .accent-stripe {
    position: absolute;
    left: 0;
    top: 1048px;
    width: 100%;
    height: 6px;
    background: var(--brand-blue);
  }
  .contact-footer {
    position: absolute;
    left: 0;
    top: 1054px;
    width: 100%;
    height: 96px;
    background: var(--footer-black);
    color: var(--footer-text);
    font-size: 16px;
    text-align: center;
  }
  .contact-address {
    position: absolute;
    top: 26px;
    width: 100%;
  }
  .contact-line {
    position: absolute;
    top: 49px;
    width: 100%;
    display: flex;
    justify-content: center;
    align-items: center;
    gap: 6px;
  }
  .contact-item {
    display: inline-flex;
    align-items: center;
    gap: 5px;
  }
  .contact-item + .contact-item { margin-left: 6px; }
  .contact-icon { width: 14px; height: 14px; fill: var(--brand-blue); }
</style>
</head>
<body>
  <main class="notepad">
    <header class="brand">
      <span class="brand-dot"></span>
      <span class="brand-name">Meridian Hose &amp; Couplings</span>
    </header>

    <div class="ruled-area"></div>

    <div class="accent-stripe"></div>

    <footer class="contact-footer">
      <p class="contact-address">42 Calloway St, Northfield SA 5085</p>
      <p class="contact-line">
        <span class="contact-item">
          <svg class="contact-icon" viewBox="0 0 24 24" aria-hidden="true">
            <path d="M6.6 10.8a15.1 15.1 0 0 0 6.6 6.6l2.2-2.2a1 1 0 0 1 1-.25 11.4 11.4 0 0 0 3.6.57 1 1 0 0 1 1 1V20a1 1 0 0 1-1 1A17 17 0 0 1 3 4a1 1 0 0 1 1-1h3.5a1 1 0 0 1 1 1c0 1.25.2 2.45.57 3.57a1 1 0 0 1-.25 1z"/>
          </svg>
          0400 555 213
        </span>
        <span class="contact-item">
          <svg class="contact-icon" viewBox="0 0 24 24" aria-hidden="true">
            <path d="M2 5h20v14H2z M3 6l9 7 9-7" />
          </svg>
          hello@meridianhose.com.au
        </span>
        <span class="contact-item">
          <svg class="contact-icon" viewBox="0 0 24 24" aria-hidden="true">
            <circle cx="12" cy="12" r="10"/>
          </svg>
          www.meridianhose.com.au
        </span>
      </p>
    </footer>
  </main>
</body>
</html>
```